Coastline Premier Retreats Business Card Design

Design a business card for Coastline Premier Retreats. Look at the website for colors and reference. Card should have logo, name, title, office number, mobile number, email, URL and a tagline like, "Luxury Hotel & Resort Email Marketing" (This might change).

https://www.coastlinepremierretreats.example

The rest I will leave up to your imagination.

Contact Information for Business Card

Logo, name, title, office number, mobile number, email, URL and a tagline like, "Luxury Hotel & Resort Email Marketing" (This might change).

```html
<!DOCTYPE html>
<html lang="en">
<head>
<meta charset="utf-8">
<title>Coastline Premier Retreats – Business Card</title>
<link rel="stylesheet" href="https://fonts.googleapis.com/css2?family=Open+Sans:wght@400;600;700&display=swap">
<style>
  :root {
    --backdrop: #232324;
    --card: #1e1e21;
    --card-light: #26262a;
    --ink: #ffffff;
    --ink-soft: #e6e6e8;
    --accent: #f37021;
    --emboss: #1a1a1d;
  }
  * { margin: 0; padding: 0; box-sizing: border-box; }
  html, body {
    width: 1200px; height: 780px; overflow: hidden;
    background: var(--backdrop);
    font-family: "Open Sans", Arial, sans-serif;
  }
  .canvas {
    position: relative; width: 1200px; height: 780px;
    display: flex; align-items: center; justify-content: center; gap: 48px;
  }
  .card {
    position: relative; width: 525px; height: 300px;
    background: var(--card); overflow: hidden;
    box-shadow: 0 18px 40px rgba(0,0,0,.45);
  }
  .card-facet { position: absolute; inset: 0; width: 100%; height: 100%; }

  /* front */
  .brand {
    position: absolute; left: 34px; top: 34px;
    display: flex; align-items: center; gap: 10px;
  }
  .brand-square { width: 12px; height: 12px; background: var(--accent); }
  .brand-name {
    font-weight: 700; font-size: 19px; letter-spacing: .06em;
    text-transform: uppercase; color: var(--ink);
  }
  .details {
    position: absolute; right: 34px; top: 100px; bottom: 22px;
    display: flex; flex-direction: column; justify-content: space-between;
    align-items: flex-end; text-align: right;
  }
  .person-name { font-size: 25px; font-weight: 700; line-height: 30px; }
  .person-name .first { color: var(--accent); }
  .person-name .last { color: var(--ink); }
  .person-title { font-size: 13px; line-height: 18px; color: var(--ink); margin-top: 2px; }
  .tagline { font-size: 12px; line-height: 16px; color: var(--accent); margin-top: 4px; }
  .contact-list { list-style: none; }
  .contact-item {
    display: flex; justify-content: flex-end; align-items: center; gap: 8px;
    font-size: 12px; color: var(--ink-soft); line-height: 18px;
  }
  .contact-icon { width: 12px; height: 12px; flex: none; }

  /* back */
  .card-back { background: var(--card-light); }
  .back-brand {
    position: absolute; inset: 0; display: flex; align-items: center; justify-content: center;
  }
  .back-brand-name {
    font-weight: 700; font-size: 26px; letter-spacing: .08em; text-transform: uppercase;
    color: var(--emboss);
  }
</style>
</head>
<body>
<main class="canvas">

  <section class="card card-front" aria-label="Business card front">
    <svg class="card-facet" viewBox="0 0 525 300" preserveAspectRatio="none" aria-hidden="true">
      <defs>
        <linearGradient id="facet-shade" x1="0" y1="0" x2="1" y2="0">
          <stop offset="0" stop-color="#2a2a2e" stop-opacity="0"/>
          <stop offset=".5" stop-color="#2a2a2e" stop-opacity=".9"/>
          <stop offset="1" stop-color="#28282c" stop-opacity=".6"/>
        </linearGradient>
      </defs>
      <polygon points="0,118 525,0 525,300 0,300" fill="#1c1c1f"/>
      <polygon points="0,118 525,210 525,0" fill="url(#facet-shade)" opacity=".55"/>
      <line x1="0" y1="118" x2="525" y2="210" stroke="#151517" stroke-width="2"/>
    </svg>

    <div class="brand">
      <span class="brand-square"></span>
      <span class="brand-name">Coastline Premier Retreats</span>
    </div>

    <div class="details">
      <div class="identity">
        <h1 class="person-name"><span class="first">Marina</span> <span class="last">Kovalenko</span></h1>
        <p class="person-title">Co-Founder</p>
        <p class="tagline">Luxury Hotel &amp;<br>Resort Email Marketing</p>
      </div>

      <ul class="contact-list">
        <li class="contact-item">(555) 014-2290
          <svg class="contact-icon" viewBox="0 0 12 12" aria-hidden="true"><path d="M2.5 1h2l1 3-1.3 1a6 6 0 0 0 2.8 2.8l1-1.3 3 1v2a1 1 0 0 1-1 1A9.5 9.5 0 0 1 1.5 2a1 1 0 0 1 1-1z" fill="var(--accent)"/></svg>
        </li>
        <li class="contact-item">(555) 017-3346
          <svg class="contact-icon" viewBox="0 0 12 12" aria-hidden="true"><rect x="3" y="1" width="6" height="10" rx="1" fill="none" stroke="var(--accent)" stroke-width="1.2"/><circle cx="6" cy="9.3" r=".6" fill="var(--accent)"/></svg>
        </li>
        <li class="contact-item">www.coastlinepremierretreats.example
          <svg class="contact-icon" viewBox="0 0 12 12" aria-hidden="true"><circle cx="6" cy="6" r="5" fill="none" stroke="var(--accent)" stroke-width="1.2"/><path d="M1 6h10M6 1c-2 2.5-2 7.5 0 10M6 1c2 2.5 2 7.5 0 10" fill="none" stroke="var(--accent)" stroke-width="1"/></svg>
        </li>
        <li class="contact-item">info@coastlinepremierretreats.example
          <svg class="contact-icon" viewBox="0 0 12 12" aria-hidden="true"><rect x="1" y="2.5" width="10" height="7" fill="var(--accent)"/><path d="M1 2.5l5 4 5-4" fill="none" stroke="var(--card)" stroke-width="1"/></svg>
        </li>
      </ul>
    </div>
  </section>

  <section class="card card-back" aria-label="Business card back">
    <div class="back-brand">
      <span class="back-brand-name">Coastline Premier Retreats</span>
    </div>
  </section>

</main>
</body>
</html>
```